Indy Film Production Company/Studio

We need a business card designed from an existing logo. We are a digital studio/production company that caters to creating genre entertainment, like Action, Horror, and martial arts. The card along with the logo will be used to Brand the company from letter heads to banners. The design will also be used for postcards and Brochures. It should be professional and masculine.
Updates

Thank you to all the designers who have participated. I'm narrowing down who it will be. Thank you again.

Target Market(s)

Investors, Networks, Producers, and actors

Industry/Entity Type

Film Production

Contact Information for Business Card

Teodoro Valbuena
Producer/Writer/Director
www.kestrelpicturehouse.example

Requirements
Must have
• Website address, Facebook icon and Twitter icon possibly in the back of the card.
Nice to have
• Logline of Company: Follow The Action.

```html
<!DOCTYPE html>
<html lang="en">
<head>
<meta charset="utf-8">
<title>Kestrel Picture House — Business Card</title>
<link rel="stylesheet" href="https://fonts.googleapis.com/css2?family=Montserrat:ital,wght@0,800;1,800&family=Roboto:wght@400&display=swap">
<style>
  :root {
    --backdrop: #a9a7a7;
    --card: #f1f1f0;
    --brand-red: #d2352c;
    --ink: #1c1c1c;
    --ink-soft: #2e2e2e;
    --rule: #dcdcdc;
  }
  * { margin: 0; padding: 0; box-sizing: border-box; }
  html, body {
    width: 1200px;
    height: 1200px;
    overflow: hidden;
    background: var(--backdrop);
  }
  .canvas {
    position: relative;
    width: 1200px;
    height: 1200px;
  }
  .card {
    position: absolute;
    width: 712px;
    height: 418px;
    background: var(--card);
  }
  .card--front { left: 238px; top: 119px; }
  .card--back  { left: 230px; top: 644px; }

  .wordmark {
    position: absolute;
    font-family: "Montserrat", sans-serif;
    font-weight: 800;
    color: var(--brand-red);
    text-transform: uppercase;
    text-align: center;
    line-height: 1;
  }
  .wordmark__main { display: block; }
  .wordmark__sub  { display: block; }

  .card--front .wordmark {
    left: 0; right: 0;
    top: 138px;
  }
  .card--front .wordmark__main { font-size: 82px; letter-spacing: 2px; }
  .card--front .wordmark__sub  { font-size: 31px; letter-spacing: 1px; margin-top: 14px; }

  .card--back .wordmark {
    left: 50px;
    width: 250px;
    top: 150px;
  }
  .card--back .wordmark__main { font-size: 50px; letter-spacing: 1px; }
  .card--back .wordmark__sub  { font-size: 19px; letter-spacing: 0.5px; margin-top: 9px; }

  .divider {
    position: absolute;
    left: 338px;
    top: 72px;
    width: 1px;
    height: 276px;
    background: var(--rule);
  }

  .contact {
    position: absolute;
    left: 375px;
    top: 96px;
    font-family: "Roboto", sans-serif;
    color: var(--ink-soft);
  }
  .contact__name {
    font-family: "Montserrat", sans-serif;
    font-style: italic;
    font-weight: 800;
    font-size: 26px;
    color: var(--ink);
    line-height: 1.1;
  }
  .contact__title {
    font-size: 16px;
    color: var(--brand-red);
    margin-top: 7px;
  }
  .contact__list {
    list-style: none;
    margin-top: 26px;
    font-size: 18px;
    line-height: 28.5px;
  }
  .contact__item { display: flex; align-items: center; }
  .contact__icon {
    width: 16px;
    height: 14px;
    margin-right: 18px;
    fill: var(--brand-red);
    flex: none;
  }
  .contact__item--social { margin-top: 4px; }
  .social-dot {
    width: 16px;
    height: 16px;
    border-radius: 50%;
    background: var(--brand-red);
    margin-right: 8px;
    flex: none;
  }
  .social-dot + .social-dot { margin-right: 12px; }
</style>
</head>
<body>
<main class="canvas">

  <section class="card card--front" aria-label="Card front">
    <h1 class="wordmark">
      <span class="wordmark__main">Kestrel</span>
      <span class="wordmark__sub">Picture House</span>
    </h1>
  </section>

  <section class="card card--back" aria-label="Card back">
    <p class="wordmark">
      <span class="wordmark__main">Kestrel</span>
      <span class="wordmark__sub">Picture House</span>
    </p>

    <div class="divider"></div>

    <div class="contact">
      <h2 class="contact__name">Teodoro Valbuena</h2>
      <p class="contact__title">Producer / Writer / Director</p>
      <ul class="contact__list">
        <li class="contact__item">
          <svg class="contact__icon" viewBox="0 0 16 14" aria-hidden="true">
            <path d="M1 4 Q8 -1 15 4 L13 6 L11 4.5 L5 4.5 L3 6 Z"/>
            <path d="M4 6.5 L12 6.5 L14 13 L2 13 Z"/>
          </svg>
          +00 111 222 3333
        </li>
        <li class="contact__item">
          <svg class="contact__icon" viewBox="0 0 16 14" aria-hidden="true">
            <path d="M1 2 L15 2 L8 7.5 Z"/>
            <path d="M1 4 L8 9.5 L15 4 L15 12 L1 12 Z"/>
          </svg>
          yourname@yourwebsite.com
        </li>
        <li class="contact__item">
          <svg class="contact__icon" viewBox="0 0 16 16" aria-hidden="true">
            <path d="M8 1 A7 7 0 1 0 8.01 1 Z M8 3 A5 5 0 1 1 7.99 3 Z" fill-rule="evenodd"/>
            <rect x="2" y="7.2" width="12" height="1.6"/>
            <rect x="7.2" y="2" width="1.6" height="12"/>
          </svg>
          www.kestrelpicturehouse.example
        </li>
        <li class="contact__item">Your Long Commercial or</li>
        <li class="contact__item">business address in 2 line</li>
        <li class="contact__item contact__item--social">
          <span class="social-dot" aria-hidden="true"></span>
          <span class="social-dot" aria-hidden="true"></span>
          /kestrelpicturehouse
        </li>
      </ul>
    </div>
  </section>

</main>
</body>
</html>
```